Business Intelligence Application - Reporting Menu and Report Criteria Design

Looking for a fresh, effective and user friendly view for the menu structure and reporting criteria screen format for a business reporting application. Initial format completed, content structure is in place, but we need the 'wow' design.. as its a serious professional report/BI tool it has to fall within certain guidelines for clarity and graphics..but we want it to be slick, friendly, great user experience. There is a large amount of complex content to fit into a small space and we need it to be very inviting, modern and intuitive.. If interested, please review the attachment. We have live screens in operation, but feel these could be improved and looking forward to seeing what great creative suggestions could be made. Please review work done to date in the attached.. We are not looking for a total re-design of everything, all the basic business content/structure is there.. but tell us what we could do to improve this in terms of graphic design... particularly the criteria screens.. thanks!
Updates

Reason: Need a few more days to review designs - thanks for all submissions so far, we will make a selection shortly.

Target Market(s)

Business analysts, hotel operations teams, finance analysts hospitality industry

Industry/Entity Type

Hospitality

Coding

Coded - Design and coding required

Number of Pages Required

4 page

Font styles to use
Sans Serif
Other font styles liked:
• Candara, please see example in deck

Colors
3276b5
3176b5
0255a3
85acd3
33a6d7
cee9f5
85cae6

Requirements
Must have
• sharp clear, logical menu structure, (currently it has 'clicks to sub-menus, we need hover over, slide to sub-menus..) colour, styling.. and most focus on revision of criteria.. right now is somewhat heavy, cumbersome.. keep colour and friendly intuitive process steps.. its heavy analytical stuff.. best of luck!
Should not have
• No grey fonts on white or grey screens! many business apps are not readable or sharp.. or fonts are too small.. colourless, so please avoid that.. see our deck - sharp dark (navy) or black fonts on white, or light shading..

```html
<!DOCTYPE html>
<html lang="en">
<head>
<meta charset="utf-8">
<title>Yieldwise – Property Search</title>
<link href="https://fonts.googleapis.com/css2?family=Mulish:wght@400;600;700;800&display=swap" rel="stylesheet">
<style>
:root{
  --navy:#011838;
  --nav:#0457a6;
  --nav-active:#2e8fcf;
  --nav-accent:#4fb3d9;
  --nav-line:#3a7fc0;
  --bg-top:#2f9fd6;
  --bg-bottom:#0a61ad;
  --panel:#4fb1dd;
  --menu:#2b92cf;
  --menu-line:#5aaedc;
  --submenu:#0256a5;
  --white:#ffffff;
  --icon:#1a88d6;
  --teal:#2fd3e0;
  --input-top:#ffffff;
  --input-bottom:#ececec;
  --input-text:#555e66;
  --button:#0256a5;
  --footer:#e1e1e1;
  --footer-text:#5a5a5a;
}
*{box-sizing:border-box;margin:0;padding:0}
html,body{width:1200px;height:664px;overflow:hidden}
body{font-family:"Mulish",sans-serif;position:relative;background:var(--white)}
.topbar{position:absolute;left:0;top:0;width:1200px;height:113px;background:var(--navy)}
.brand{position:absolute;left:97px;top:38px;display:flex;align-items:center;gap:14px}
.brand-dot{width:32px;height:32px;border-radius:50%;background:var(--teal)}
.brand-name{font-size:28px;font-weight:700;color:var(--white);letter-spacing:.2px}
.user{position:absolute;left:781px;top:35px;display:flex;align-items:center;gap:9px}
.avatar{width:44px;height:44px;border-radius:50%;background:linear-gradient(#c9a894,#6d5b52)}
.user-text{color:#e8eef7;font-size:15px;line-height:21px}
.divider{position:absolute;top:40px;width:1px;height:38px;background:#1c3557}
.icon{position:absolute}
.mainnav{position:absolute;left:0;top:113px;width:1200px;height:51px;background:var(--nav)}
.nav-item{position:absolute;top:0;height:51px;display:flex;align-items:center;justify-content:center;color:var(--white);font-size:13px;font-weight:700;border-left:1px solid var(--nav-line);gap:4px}
.nav-item.active{background:var(--nav-active);border-left:none}
.nav-item.accent{background:var(--nav-accent)}
.nav-badge{width:20px;height:20px;border-radius:50%;background:#d89a4c}
.stage{position:absolute;left:0;top:164px;width:1200px;height:425px;background:linear-gradient(var(--bg-top),var(--bg-bottom))}
.criteria{position:absolute;left:112px;top:183px;width:973px;height:320px;background:var(--panel)}
.field-label{position:absolute;color:var(--white);font-size:18px;font-weight:700;letter-spacing:.2px}
.field-label.plain{font-weight:600;text-transform:none}
.field{position:absolute;height:43px;background:linear-gradient(var(--input-top),var(--input-bottom));border:1px solid #d2d2d2;color:var(--input-text);font-size:16px;padding:0 17px;display:flex;align-items:center}
.search-btn{position:absolute;left:820px;top:416px;width:214px;height:50px;background:var(--button);color:var(--white);font-size:21px;font-weight:700;display:flex;align-items:center;justify-content:center;border-radius:2px}
.dropdown{position:absolute;left:72px;top:164px;width:265px;height:173px;background:var(--menu);box-shadow:0 2px 6px rgba(0,0,0,.2)}
.drop-item{position:absolute;left:0;width:265px;height:37px;padding-left:33px;display:flex;align-items:center;color:var(--white);font-size:16px;border-bottom:1px solid var(--menu-line)}
.drop-item.open{background:var(--submenu);left:-2px;width:267px;border-bottom:none}
.submenu{position:absolute;left:337px;top:244px;width:210px;height:259px;background:var(--submenu)}
.sub-item{position:absolute;left:33px;color:var(--white);font-size:14px}
.footer{position:absolute;left:0;top:589px;width:1200px;height:75px;background:var(--footer);display:flex;justify-content:center;padding-top:25px;color:var(--footer-text);font-size:13px;letter-spacing:.1px}
</style>
</head>
<body>
<header class="topbar">
  <div class="brand"><span class="brand-dot"></span><span class="brand-name">Yieldwise</span></div>
  <div class="user">
    <div class="avatar" role="img" aria-label="Admin profile photo"></div>
    <div class="user-text">Welcome<br><strong style="font-weight:600">Admin</strong></div>
  </div>
  <span class="divider" style="left:919px"></span>
  <svg class="icon" style="left:946px;top:42px" width="28" height="30" viewBox="0 0 28 30" aria-label="Notifications">
    <path d="M14 2c-5 0-8 4-8 9v7l-3 4v2h22v-2l-3-4v-7c0-5-3-9-8-9z" fill="var(--icon)"/>
    <circle cx="14" cy="26.5" r="3" fill="var(--icon)"/>
  </svg>
  <span class="divider" style="left:1005px"></span>
  <svg class="icon" style="left:1036px;top:46px" width="28" height="24" viewBox="0 0 28 24" aria-label="Share">
    <path d="M17 1l10 9-10 9v-5.5C9 13.5 5 16 2 22 2.5 13 7 7 17 6.5z" fill="var(--icon)"/>
  </svg>
</header>

<nav class="mainnav">
  <div class="nav-item active" style="left:73px;width:68px">Admin</div>
  <div class="nav-item" style="left:141px;width:96px">Management</div>
  <div class="nav-item" style="left:237px;width:144px">Rooms Performance</div>
  <div class="nav-item" style="left:381px;width:133px">Revenue Summary</div>
  <div class="nav-item" style="left:514px;width:112px">Demand &amp; Risk</div>
  <div class="nav-item" style="left:626px;width:133px">Inventory Analysis</div>
  <div class="nav-item" style="left:759px;width:89px">Placeholder</div>
  <div class="nav-item accent" style="left:848px;width:141px"><span class="nav-badge" role="img" aria-label="Cartoon mascot icon"></span>Property Search</div>
  <div class="nav-item" style="left:989px;width:43px">Intel</div>
  <div class="nav-item" style="left:1032px;width:71px;border-right:1px solid var(--nav-line)">Planning</div>
</nav>

<main class="stage"></main>
<section class="criteria"></section>
<div class="field-label" style="left:460px;top:226px">SEARCH ID</div>
<div class="field" style="left:460px;top:257px;width:279px"></div>
<div class="field-label" style="left:753px;top:226px">SEARCH PRODUCT</div>
<div class="field" style="left:751px;top:257px;width:283px"></div>
<div class="field-label" style="left:158px;top:327px">DIVISIONS</div>
<div class="field" style="left:157px;top:358px;width:283px">Europe</div>
<div class="field-label" style="left:460px;top:327px">COUNTRY</div>
<div class="field" style="left:460px;top:358px;width:279px">England</div>
<div class="field-label plain" style="left:751px;top:325px">Areas</div>
<div class="field" style="left:751px;top:358px;width:283px">Central London</div>
<div class="search-btn">SEARCH</div>

<div class="dropdown">
  <div class="drop-item" style="top:0">Registration</div>
  <div class="drop-item" style="top:37px">User Access</div>
  <div class="drop-item open" style="top:74px">Setup</div>
  <div class="drop-item" style="top:111px;border-bottom:none">Data Imports</div>
</div>
<div class="submenu">
  <div class="sub-item" style="top:18px">Market Segments</div>
  <div class="sub-item" style="top:46px">Banquet &amp; Catering</div>
  <div class="sub-item" style="top:74px">Outlets/F&amp;B Service</div>
  <div class="sub-item" style="top:102px">Other Income</div>
  <div class="sub-item" style="top:130px">Impact Dates</div>
  <div class="sub-item" style="top:158px">Inventory</div>
  <div class="sub-item" style="top:186px">Geo/Location</div>
  <div class="sub-item" style="top:214px">Distribution Channels</div>
</div>

<footer class="footer">© 2017 Company Name&nbsp; All right reserved&nbsp; Term of Use</footer>
</body>
</html>
```